Telecommunications/Power civil contractor needs business card design

Were a new telecommunications/power underground civil contractor that is looking for a new business card design. Our company colours are silver or grey and orange. Feel free to use the white background logo or the black background logo.

Target Market(s)

Local contractors, utility companies, private sector mining/energy companies, developers.

Industry/Entity Type

Telecommunications

Contact Information for Business Card

Each card will need the following info:
Persons name:
Title:
E-mail:
Phone number:
Shop Address:
Mailing Address:

Requirements
Must have
• Each card will need the following info:
• Persons name:
• Title:
• E-mail:
• Phone number:
• Shop Address:
• Mailing Address:

```html
<!DOCTYPE html>
<html lang="en">
<head>
<meta charset="utf-8">
<title>Ridgeline Trench Works – Business Card</title>
<link rel="stylesheet" href="https://fonts.googleapis.com/css2?family=Open+Sans:ital,wght@0,400;0,700;1,400&display=swap">
<style>
  :root {
    --stage: #e9e7e4;
    --orange: #f15a24;
    --orange-light: #f6875e;
    --white: #ffffff;
    --grey-dark: #5f6062;
    --grey-mid: #8e8f91;
    --grey-light: #c9cacb;
    --swoosh: #9a9b9d;
  }
  * { margin: 0; padding: 0; box-sizing: border-box; }
  html, body {
    width: 1200px; height: 843px; overflow: hidden;
    background: var(--stage);
    font-family: "Open Sans", Arial, sans-serif;
  }
  .stage {
    width: 1200px; height: 843px;
    display: flex; flex-direction: column;
    align-items: center; justify-content: center; gap: 29px;
  }
  .card {
    position: relative;
    width: 660px; height: 377px;
    box-shadow: 0 8px 24px rgba(0,0,0,.18);
    overflow: hidden;
  }
  .card-back {
    background: linear-gradient(90deg, var(--grey-dark) 0%, var(--grey-mid) 45%, var(--grey-light) 70%, var(--grey-mid) 100%);
    display: flex; align-items: center; justify-content: center;
  }
  .back-brand {
    display: flex; align-items: center; gap: 16px;
    color: var(--white); font-weight: 700; font-size: 26px; letter-spacing: 1px;
    text-transform: uppercase;
  }
  .brand-dot {
    width: 46px; height: 46px; border-radius: 50%;
    border: 5px solid var(--white);
  }
  .card-front svg.front-shapes { position: absolute; inset: 0; }
  .contact {
    position: absolute; left: 44px; top: 44px; color: var(--white);
  }
  .contact .person { font-size: 22px; font-weight: 700; line-height: 1.1; }
  .contact .role { font-size: 14px; font-style: italic; margin-top: 2px; }
  .contact .details { margin-top: 96px; font-size: 14.5px; line-height: 1.35; }
  .contact .line { display: flex; align-items: center; gap: 9px; }
  .contact .line svg { width: 13px; height: 13px; flex: none; }
  .front-brand {
    position: absolute; left: 432px; top: 168px;
    display: flex; align-items: center; gap: 10px;
    color: var(--orange); font-weight: 700; font-size: 19px; line-height: 1.1;
    text-transform: uppercase; letter-spacing: .5px;
  }
  .front-brand .brand-dot { width: 30px; height: 30px; border: 4px solid var(--orange); }
</style>
</head>
<body>
<main class="stage">
  <section class="card card-back" aria-label="Card back">
    <div class="back-brand"><span class="brand-dot"></span>Ridgeline Trench Works</div>
  </section>

  <section class="card card-front" aria-label="Card front">
    <svg class="front-shapes" viewBox="0 0 660 377" width="660" height="377" aria-hidden="true">
      <defs>
        <linearGradient id="orangeFace" x1="0" y1="0" x2="1" y2="0">
          <stop offset="0" stop-color="var(--orange)"/>
          <stop offset=".55" stop-color="var(--orange-light)"/>
          <stop offset="1" stop-color="var(--orange)"/>
        </linearGradient>
      </defs>
      <rect width="660" height="377" fill="url(#orangeFace)"/>
      <circle cx="505" cy="215" r="218" fill="var(--swoosh)"/>
      <rect x="505" y="0" width="155" height="377" fill="var(--white)"/>
      <circle cx="518" cy="212" r="210" fill="var(--white)"/>
    </svg>

    <div class="contact">
      <div class="person">Daniel Reyes</div>
      <div class="role">CEO/Founder</div>
      <div class="details">
        <div>412 Alder Court</div>
        <div>Fairbanks, Alaska 99701</div>
        <div class="line">
          <svg viewBox="0 0 16 16"><path fill="#fff" d="M3.5 1l2.5 3-1.5 2c1 2 2.5 3.5 4.5 4.5l2-1.5 3 2.5-1.5 2.5C7 15 1 9 1 2.5z"/></svg>
          907 555 0142
        </div>
        <div class="line">
          <svg viewBox="0 0 16 16"><rect x="1" y="3" width="14" height="10" fill="#fff"/><path d="M1 3l7 6 7-6" fill="none" stroke="#f15a24" stroke-width="1.4"/></svg>
          daniel@ridgelinetrench.com
        </div>
        <div class="line">
          <svg viewBox="0 0 16 16"><circle cx="8" cy="8" r="7" fill="#fff"/><path d="M1 8h14M8 1c-3 4-3 10 0 14M8 1c3 4 3 10 0 14" fill="none" stroke="#f15a24" stroke-width="1"/></svg>
          www.ridgelinetrench.com
        </div>
      </div>
    </div>

    <div class="front-brand"><span class="brand-dot"></span><span>Ridgeline<br>Trench Works</span></div>
  </section>
</main>
</body>
</html>
```